Landing Page / Waitlist

I would like a landing page for people to sign up for a waiting list. The text on the page should include (but is not limited to):
1) Main point: The accounting system you'll love
2) Secondary points:
a. Ruthlessly efficient
b. Quietly intelligent
c. Driven by AI
I've attached a file of our logo

The design should be simple, clean, and innovative - this is an ai company

```html
<!DOCTYPE html>
<html lang="en">
<head>
<meta charset="utf-8">
<title>LedgerLoom — Join the Waitlist</title>
<link href="https://fonts.googleapis.com/css2?family=Montserrat:wght@400;500;600;700&display=swap" rel="stylesheet">
<style>
  :root {
    --ink: #2b2b2b;
    --ink-soft: #4a4a4a;
    --grey-brand: #6f6f6f;
    --blue: #0aa3f5;
    --blue-deep: #0a7fe0;
    --sky: #e3f3fd;
    --white: #ffffff;
    --rule: #e2e2e2;
  }
  * { box-sizing: border-box; margin: 0; padding: 0; }
  html, body { width: 1107px; height: 1200px; overflow: hidden; }
  body {
    font-family: "Montserrat", sans-serif;
    color: var(--ink);
    background: linear-gradient(180deg, var(--sky) 0%, #f2f9fe 40%, var(--white) 52%, var(--white) 100%);
    position: relative;
  }
  .brand {
    position: absolute; left: 0; right: 0;
    display: flex; justify-content: center; align-items: center; gap: 10px;
  }
  .brand-mark { width: 22px; height: 22px; background: var(--blue); }
  .brand-name { font-size: 30px; font-weight: 600; color: var(--grey-brand); letter-spacing: -0.5px; }
  .brand.top { top: 92px; }
  .brand.bottom { top: 1062px; }
  .headline {
    position: absolute; top: 160px; left: 0; right: 0;
    text-align: center; font-size: 46px; font-weight: 700; letter-spacing: -0.3px;
  }
  .headline span { font-weight: 400; }
  .signup { position: absolute; top: 256px; left: 285px; display: flex; gap: 21px; }
  .signup-input {
    width: 311px; height: 45px; border: none; background: var(--white);
    box-shadow: 0 4px 14px rgba(0,0,0,0.07);
    font-family: inherit; font-size: 13px; padding-left: 27px; color: var(--ink-soft);
  }
  .signup-input::placeholder { color: var(--ink-soft); }
  .signup-button {
    width: 162px; height: 45px; border: none;
    background: linear-gradient(90deg, var(--blue-deep), var(--blue));
    color: var(--white); font-family: inherit; font-size: 14px; font-weight: 500;
    box-shadow: 0 6px 14px rgba(10,127,224,0.25);
  }
  .features { position: absolute; top: 353px; left: 0; width: 100%; }
  .feature {
    position: absolute; top: 0; height: 126px; background: var(--white);
    box-shadow: 0 4px 16px rgba(0,0,0,0.07);
    display: flex; flex-direction: column; align-items: center; padding-top: 22px;
  }
  .feature-icon { width: 46px; height: 46px; border-radius: 50%; background: var(--blue); display: flex; align-items: center; justify-content: center; }
  .feature-label { margin-top: 14px; font-size: 14px; font-weight: 600; color: var(--ink); }
  .visual { position: absolute; left: 204px; top: 542px; width: 704px; height: 390px; }
  .visual-frame {
    position: absolute; left: 14px; top: 22px; width: 690px; height: 368px;
    background: var(--blue);
    clip-path: polygon(0 92%, 0 100%, 90% 100%, 100% 82%, 100% 0, 98% 0);
  }
  .visual-photo {
    position: absolute; left: 0; top: 0; width: 692px; height: 376px;
    background: radial-gradient(circle at 62% 55%, #6fb9e6 0%, #2f6a9a 30%, #1d3550 60%, #bfc6cc 100%);
    clip-path: polygon(73px 0, 100% 0, 100% 82%, 625px 100%, 0 100%, 0 73px);
  }
  .social { position: absolute; top: 1061px; left: 105px; display: flex; gap: 5px; }
  .social-dot { width: 34px; height: 34px; border-radius: 50%; background: var(--blue); }
  .legal { position: absolute; top: 1064px; left: 853px; font-size: 14px; color: var(--ink-soft); }
  .rule { position: absolute; top: 1163px; left: 0; width: 100%; height: 1px; background: var(--rule); }
  .copyright { position: absolute; top: 1172px; left: 0; right: 0; text-align: center; font-size: 14px; color: var(--ink-soft); }
</style>
</head>
<body>
  <header class="brand top">
    <span class="brand-mark"></span><span class="brand-name">LedgerLoom</span>
  </header>

  <h1 class="headline">The Accounting System <span>you’ll love.</span></h1>

  <form class="signup">
    <input class="signup-input" type="email" placeholder="Enter Your Email">
    <button class="signup-button" type="button">JOIN WAITLIST</button>
  </form>

  <section class="features">
    <div class="feature" style="left:235px;width:172px;">
      <div class="feature-icon">
        <svg width="24" height="24" viewBox="0 0 24 24" fill="none" stroke="#fff" stroke-width="2.2" stroke-linecap="round" stroke-linejoin="round">
          <polyline points="3,16 9,10 13,14 21,6"/><polyline points="16,6 21,6 21,11"/>
        </svg>
      </div>
      <div class="feature-label">Ruthlessly Efficient</div>
    </div>
    <div class="feature" style="left:465px;width:176px;">
      <div class="feature-icon">
        <svg width="24" height="24" viewBox="0 0 24 24" fill="none" stroke="#fff" stroke-width="2" stroke-linecap="round">
          <circle cx="12" cy="12" r="8"/><line x1="12" y1="4" x2="12" y2="20"/><circle cx="16" cy="9" r="1.4" fill="#fff"/><circle cx="16" cy="15" r="1.4" fill="#fff"/>
        </svg>
      </div>
      <div class="feature-label">Quietly Intelligent</div>
    </div>
    <div class="feature" style="left:696px;width:176px;">
      <div class="feature-icon">
        <svg width="24" height="24" viewBox="0 0 24 24" fill="none" stroke="#fff" stroke-width="2" stroke-linecap="round">
          <rect x="6" y="6" width="12" height="12" rx="2"/>
          <line x1="9" y1="2" x2="9" y2="5"/><line x1="15" y1="2" x2="15" y2="5"/>
          <line x1="9" y1="19" x2="9" y2="22"/><line x1="15" y1="19" x2="15" y2="22"/>
          <line x1="2" y1="9" x2="5" y2="9"/><line x1="2" y1="15" x2="5" y2="15"/>
          <line x1="19" y1="9" x2="22" y2="9"/><line x1="19" y1="15" x2="22" y2="15"/>
        </svg>
      </div>
      <div class="feature-label">Driven by AI</div>
    </div>
  </section>

  <section class="visual">
    <div class="visual-frame"></div>
    <div class="visual-photo" role="img" aria-label="Photo of hands typing on a laptop with glowing AI dashboard overlays"></div>
  </section>

  <footer>
    <nav class="social">
      <span class="social-dot" aria-label="Social link"></span>
      <span class="social-dot" aria-label="Social link"></span>
      <span class="social-dot" aria-label="Social link"></span>
    </nav>
    <div class="brand bottom">
      <span class="brand-mark"></span><span class="brand-name">LedgerLoom</span>
    </div>
    <div class="legal">Privacy Policy | Terms</div>
    <div class="rule"></div>
    <p class="copyright">© 2025 LedgerLoom. All rights reserved.</p>
  </footer>
</body>
</html>
```